Top Pour Web site design

The aim of Top Pour is to provide an online service which allows customers to pre-order drinks and gain incentives such as fast entry, special offers (drinks, entry fees), as well as allowing customers to compare drinking establishments based upon costs and ratings.

what is required is the design of the pages stated below completed to the specifications.

Target Market(s)

The target market of Top Pour is men and women between the ages of 18 to 26 mainly. Within the age range of 18 to 26 the more specific target groups

Industry/Entity Type

Online

Requirements
Must have
• What is required to be designed

Website to be viewable on different systems e.g desktop, laptop and for mobile devices a mobile friendly page

Home page

Logo
Company name
Log in
Sign up
Help
Social media links, Follow us link

Bar, pub, club search function
Search by postcode, establishment type, distance

Pictorial instructions of how to use the site like ( quick dine). The stages are 1) select location 2) build order and pay 3) pick up from bar

Pre load results of establishments

Drinking establishment sign up

Map showing search results

List of results

My basket window which shows your order

Pop out box for customer sign up

Buttons for FAQ, general information, company information, Privacy policy ect at bottom of page

The home page is required to be Clear, simple, easy to use and stylish but not over the top with to much information which will confuse the customers. The preloaded results need to be obvious and where can be seen. The pictorial instructions should go below the preloaded results. Once the search criteria has been filled in and has been submitted the preloaded results and pictorial instructions will be removed and be replaced by the map and search results.

Drinking establishment personal page requires

Details of drinking establishment (name, address, contact, map)
list of drinks avliable
My basket
Special Offers
Gallery
Calendar
Reviews section at the bottom

When a person clicks on a drinking establishment page what that person should see when they open the page is company name logo
with a list of the drinks they offer and special offers. Tabs or buttons for gallery, establishment details, calender and special offers should be located along top or down the left. when they are clicked on they will replace the menu.

The colour scheme is based around the logo which is attached. We do not want any pink or overly bright colours which would not go with the logo.

A site which we like is this one
http://www.quick-dine.example.co.uk/
this site is perfect simple, clear but also good looking. If you need inspiration you should use this site as a starting point.
Should not have
• what should be avoided is a site which like this one http://platepoint.example.co.uk/~beta/?gclid=XQMWpLaRtnfGDsHYbTqeKZPLv

it is to complicated with bad font and colours. The site just feels cheesy and not classy. we like very little about this site

```html
<!DOCTYPE html>
<html lang="en">
<head>
<meta charset="utf-8">
<title>Top Pour</title>
<link href="https://fonts.googleapis.com/css2?family=Cabin+Sketch:wght@400;700&family=Open+Sans:wght@400;600;700&display=swap" rel="stylesheet">
<style>
:root{
  --navy:#1e3a8c;
  --navy-dark:#16307a;
  --ink:#1b1f7a;
  --purple:#3a3a96;
  --orange:#f7931e;
  --orange-light:#fbb040;
  --text:#444;
  --grey-band:#e8e8e8;
  --grey-mid:#8a8a8a;
  --paper:#fff;
  --dash:#c8853a;
}
*{box-sizing:border-box;margin:0;padding:0}
html,body{width:1187px;height:1200px;overflow:hidden;background:#fff}
body{position:relative;font-family:'Open Sans',sans-serif;color:var(--text)}
.abs{position:absolute}

.header-band{left:0;top:0;width:1187px;height:196px;background:linear-gradient(#e3e3e3,#ececec)}
.brand{left:184px;top:17px;display:flex;align-items:center;gap:12px}
.brand-mark{width:70px;height:70px;border-radius:50%;background:#cfcfcf}
.brand-name{font-weight:700;font-size:25px;color:var(--ink)}

.cart{left:551px;top:60px;font-size:12.5px;color:#666;display:flex;align-items:center;gap:5px}
.cart .num{color:var(--orange);font-weight:600}
.cart .checkout{margin-left:4px;border:1px solid #bbb;background:linear-gradient(#f4f4f4,#dcdcdc);padding:2px 9px;font-size:12.5px;color:#555}
.account{left:816px;top:61px;font-size:14.5px;font-weight:600;color:#555}
.help{left:927px;top:58px;background:#fff;border:1px solid #ccc;border-radius:5px;padding:3px 9px;font-size:12px;color:var(--ink)}
.social{display:flex;gap:5px}
.social span{width:22px;height:22px;border-radius:50%;background:var(--purple);display:block}
.social-top{left:903px;top:25px}

.search{left:183px;top:130px;width:821px;height:124px;background:var(--navy);border-radius:16px;box-shadow:0 10px 10px -8px rgba(0,0,0,.25)}
.search-title{left:240px;top:140px;font-family:'Cabin Sketch',sans-serif;font-size:40px;color:#fff;font-weight:700}
.search-title em{font-style:normal;color:var(--orange-light)}
.field{top:200px;height:31px;background:#fff;border:1px solid #c9c9c9;font-size:14px;color:#555;padding:6px 9px;display:flex;justify-content:space-between;align-items:center}
.field .caret{width:0;height:0;border-left:4px solid transparent;border-right:4px solid transparent;border-top:6px solid #333}
.search-btn{left:765px;top:199px;width:156px;height:32px;background:linear-gradient(var(--orange-light),var(--orange));border:1px solid #d86e00;font-weight:700;font-size:16px;color:#7a2e00;display:flex;align-items:center;justify-content:center;gap:6px}

.section-title{left:183px;top:283px;font-family:'Cabin Sketch',sans-serif;font-size:40px;color:#444;font-weight:700}

.venue{width:380px;height:121px;border-bottom:1px dashed var(--dash)}
.venue .thumb{position:absolute;left:0;top:0;width:78px;height:78px;border:1px solid #ddd;box-shadow:0 1px 3px rgba(0,0,0,.15)}
.venue h3{position:absolute;left:87px;top:0;font-size:14.5px;font-weight:700;color:var(--ink)}
.venue p{position:absolute;left:87px;top:25px;font-size:12.5px;color:#444;white-space:nowrap}
.venue .add{position:absolute;left:87px;top:48px;width:100px;height:31px;background:linear-gradient(var(--orange-light),var(--orange));font-size:12px;font-weight:700;color:#7a2e00;display:flex;align-items:center;justify-content:center;box-shadow:0 2px 3px rgba(0,0,0,.2)}

.how-band{left:0;top:754px;width:1187px;height:360px;background:var(--grey-band);border-top:2px solid #aaa}
.how-label{left:480px;top:725px;width:229px;height:44px;background:var(--grey-mid);color:#fff;font-family:'Cabin Sketch',sans-serif;font-size:30px;font-weight:700;display:flex;align-items:center;justify-content:center}
.step{top:828px;width:256px;height:188px;background:var(--paper);box-shadow:0 8px 8px -4px rgba(0,0,0,.3)}
.step .tape{position:absolute;left:88px;top:-14px;width:96px;height:26px;background:rgba(200,200,200,.8)}
.step .num{position:absolute;left:29px;top:15px;width:27px;height:31px;border-radius:50%;background:var(--purple);color:#fff;font-family:'Cabin Sketch',sans-serif;font-weight:700;font-size:20px;display:flex;align-items:center;justify-content:center}
.step .art{position:absolute;left:66px;top:40px;width:130px;height:84px;border-radius:8px}
.step .cap{position:absolute;left:0;width:100%;top:145px;text-align:center;font-family:'Cabin Sketch',sans-serif;font-size:21px;color:#444}

.footer-links{left:179px;top:1122px;font-size:13px;color:var(--ink)}
.footer-links i{font-style:normal;color:#444;margin:0 4px}
.copyright{left:179px;top:1141px;font-size:12.5px;color:#555}
.social-foot{left:895px;top:1128px}
</style>
</head>
<body>

<div class="abs header-band"></div>

<div class="abs brand">
  <span class="brand-mark"></span>
  <span class="brand-name">Top Pour</span>
</div>

<div class="abs social social-top" aria-label="Follow us"><span></span><span></span><span></span><span></span></div>

<div class="abs cart">
  <svg width="14" height="12" viewBox="0 0 14 12"><path d="M0 1h3l2 7h7l2-5H4" fill="none" stroke="#555" stroke-width="1.6"/><circle cx="6" cy="10.5" r="1.2" fill="#555"/><circle cx="11" cy="10.5" r="1.2" fill="#555"/></svg>
  <span><span class="num">0</span> items | Subtotal : <span class="num">$0.0</span></span>
  <span class="checkout">Checkout</span>
</div>
<div class="abs account">Log in . Sign up</div>
<div class="abs help">NEED HELP</div>

<div class="abs search"></div>
<div class="abs search-title"><em>SEARCH</em> bar/pub/club</div>
<div class="abs field" style="left:237px;width:153px">Your Postcode</div>
<div class="abs field" style="left:407px;width:162px">Establishment Type <span class="caret"></span></div>
<div class="abs field" style="left:586px;width:162px">Distance <span class="caret"></span></div>
<div class="abs search-btn">SEARCH NOW
  <svg width="16" height="16" viewBox="0 0 16 16"><circle cx="6.5" cy="6.5" r="4.5" fill="none" stroke="#7a2e00" stroke-width="2"/><path d="M10 10l5 5" stroke="#7a2e00" stroke-width="2.4"/></svg>
</div>

<h1 class="abs section-title">Drinking establishment</h1>

<div class="abs venue" style="left:185px;top:347px">
  <div class="thumb" role="img" aria-label="Photo of a yellow cocktail" style="background:linear-gradient(#fff 40%,#f6c14a 60%,#fff)"></div>
  <h3>Duis sed lectus sit amet</h3><p>Nulla cursus ligula nec neque porttitor faucibus vel</p><span class="add">ADD TO CART</span>
</div>
<div class="abs venue" style="left:618px;top:347px">
  <div class="thumb" role="img" aria-label="Photo of a red long drink" style="background:linear-gradient(#fff 20%,#e8382c 60%,#fff)"></div>
  <h3>Morbi feugiat adipiscing</h3><p>Duis sed lectus sit amet neque viverra ornare.</p><span class="add">ADD TO CART</span>
</div>
<div class="abs venue" style="left:185px;top:468px">
  <div class="thumb" role="img" aria-label="Photo of an amber cocktail" style="background:linear-gradient(#fff 10%,#c8461a 30%,#fff 55%)"></div>
  <h3>Aenean ornar</h3><p>Morbi feugiat adipiscing nibh sit amet mollis</p><span class="add">ADD TO CART</span>
</div>
<div class="abs venue" style="left:618px;top:468px">
  <div class="thumb" role="img" aria-label="Photo of a red martini" style="background:linear-gradient(#fff 10%,#d8202c 30%,#fff 55%)"></div>
  <h3>Nullam enim magna</h3><p>Proin porttitor tellus in lacus facilisis molestie</p><span class="add">ADD TO CART</span>
</div>
<div class="abs venue" style="left:185px;top:589px">
  <div class="thumb" role="img" aria-label="Photo of an orange cocktail" style="background:linear-gradient(#fff 10%,#ef5a1e 45%,#fff 75%)"></div>
  <h3>Vestibulum eu metus</h3><p>Nullam enim magna, laoreet ut laoreet eleifend</p><span class="add">ADD TO CART</span>
</div>
<div class="abs venue" style="left:618px;top:589px">
  <div class="thumb" role="img" aria-label="Photo of apple juice beside an apple" style="background:linear-gradient(90deg,#c8402a 20%,#f2c55a 60%,#fff)"></div>
  <h3>Etiam tempor sapien</h3><p>Phasellus pharetra arcu et est vulputate aliquet</p><span class="add">ADD TO CART</span>
</div>

<div class="abs how-band"></div>
<h2 class="abs how-label">How it Works</h2>

<div class="abs step" style="left:178px">
  <span class="tape"></span><span class="num">1</span>
  <div class="art" role="img" aria-label="Illustration of a map with a magnifying glass" style="background:linear-gradient(135deg,#7cb8e8,#6fb04a)"></div>
  <div class="cap">Select Location</div>
</div>
<div class="abs step" style="left:462px">
  <span class="tape"></span><span class="num">2</span>
  <div class="art" role="img" aria-label="Illustration of a cash register" style="background:linear-gradient(#e6c35a,#b8c4d4)"></div>
  <div class="cap">build order and pay</div>
</div>
<div class="abs step" style="left:746px">
  <span class="tape"></span><span class="num">3</span>
  <div class="art" role="img" aria-label="Illustration of two glasses of red wine" style="background:linear-gradient(#fff,#9a1c3a 50%,#f0e6b0)"></div>
  <div class="cap">pick up from bar</div>
</div>

<svg class="abs" style="left:380px;top:890px" width="80" height="40" viewBox="0 0 80 40"><path d="M2 16 Q40 -2 74 34" fill="none" stroke="#777" stroke-width="1.5"/><path d="M74 34l-8-3 5-4z" fill="#777"/></svg>
<svg class="abs" style="left:667px;top:890px" width="80" height="40" viewBox="0 0 80 40"><path d="M2 16 Q40 -2 74 34" fill="none" stroke="#777" stroke-width="1.5"/><path d="M74 34l-8-3 5-4z" fill="#777"/></svg>

<nav class="abs footer-links">FAQ<i>|</i>general information<i>|</i>company information<i>|</i>Privacy policy</nav>
<p class="abs copyright">Copyright © 2013 Top Pour. All rights reserved</p>
<div class="abs social social-foot" aria-label="Follow us"><span></span><span></span><span></span><span></span></div>

</body>
</html>
```